Indoor golf coaching facility needs a flyer advertising the indoor practice program

Design a (editable/word document) flyer (similar to the attachments) but with colors red, light grey, white, and black with our logo advertising our indoor practice program. Fairway Nine Golf Practice MembershipMembers have 24/7 access to practice Clearbay & SAM PuttLabOnline scheduling Membership Options: $140/month for 4 hours of practice$200/month for unlimited 1 hour of practiceSpecial Offer:First 20 who sign up for a full-year membership before the new year save $400Contact us for more information: info@1undergolf.comwww.1undergolf.com

Target Market(s)

Golfers

Font styles to use
Sans Serif

Colors

Designer to choose only greyscale colors for use in the design.

Requirements
Must have
• Colors (red, light grey, black, white) and see above text, must be able to edit a version of it (word document) and pdf

```html
<!DOCTYPE html>
<html lang="en">
<head>
<meta charset="utf-8">
<title>Fairway Nine Golf Practice</title>
<link rel="stylesheet" href="https://fonts.googleapis.com/css2?family=Rubik:wght@500;700&family=PT+Sans:wght@400;700&display=swap">
<style>
  :root {
    --black: #161616;
    --charcoal: #262626;
    --red: #d3262c;
    --bright-red: #e8403a;
    --white: #ffffff;
    --light-grey: #e4e4e4;
    --mid-grey: #bdbdbd;
    --photo-top: #ededed;
    --photo-floor: #a9a9a9;
  }
  html, body { margin: 0; padding: 0; overflow: hidden; }
  body { width: 848px; height: 1200px; background: var(--red); }
  .flyer { position: relative; width: 848px; height: 1200px; overflow: hidden; font-family: "Rubik", sans-serif; color: var(--white); }
  .backdrop { position: absolute; inset: 0; }
  .brand-badge { position: absolute; left: 111px; top: 181px; width: 226px; height: 226px; border-radius: 50%; background: rgba(255,255,255,0.45); }
  .brand-name { position: absolute; left: 0; right: 0; top: 154px; font-family: "Rubik", sans-serif; font-weight: 700; font-size: 22px; color: var(--red); text-align: center; line-height: 1; }
  .title { position: absolute; left: 50px; top: 541px; margin: 0; font-weight: 700; font-size: 55px; line-height: 1; letter-spacing: 0.2px; white-space: nowrap; }
  .subtitle { position: absolute; left: 51px; top: 624px; margin: 0; font-weight: 700; font-size: 34px; line-height: 1; white-space: nowrap; }
  .access { position: absolute; left: 53px; top: 684px; margin: 0; font-weight: 700; font-size: 21px; line-height: 1; letter-spacing: 0.9px; white-space: nowrap; }
  .options-label { position: absolute; left: 17px; top: 764px; width: 390px; height: 58px; background: var(--white); color: var(--red); font-weight: 700; font-size: 32px; display: flex; align-items: center; justify-content: center; margin: 0; }
  .option { position: absolute; left: 22px; height: 47px; display: flex; align-items: center; }
  .option::before { content: ""; width: 15px; height: 47px; background: var(--white); margin-right: 15px; }
  .option-text { font-weight: 700; font-size: 22px; white-space: nowrap; }
  .option-basic { top: 852px; }
  .option-unlimited { top: 929px; }
  .option-unlimited .option-text { font-size: 22.8px; }
  .offer { position: absolute; left: 567px; top: 717px; width: 281px; height: 316px; background: var(--black); }
  .offer-heading { position: absolute; left: 0; right: 0; top: 36px; margin: 0; text-align: center; padding-left: 22px; color: var(--bright-red); font-weight: 700; font-size: 33px; line-height: 1; }
  .offer-lead { position: absolute; left: 0; right: 0; top: 80px; margin: 0; text-align: center; padding-left: 10px; font-weight: 700; font-size: 22px; line-height: 1; }
  .offer-details { position: absolute; left: 50px; top: 112px; margin: 0; font-family: "PT Sans", sans-serif; font-size: 23px; line-height: 32px; color: var(--light-grey); }
  .offer-details::before { content: ""; position: absolute; left: -17px; top: 15px; width: 10px; height: 10px; background: var(--white); }
  .contact { position: absolute; left: 49px; top: 1062px; width: 730px; height: 85px; background: var(--white); color: var(--red); font-family: "PT Sans", sans-serif; font-weight: 700; font-size: 22px; line-height: 32px; display: flex; flex-direction: column; align-items: center; justify-content: center; }
</style>
</head>
<body>
<main class="flyer">
  <svg class="backdrop" width="848" height="1200" viewBox="0 0 848 1200">
    <defs>
      <linearGradient id="facility-tones" x1="0" y1="0" x2="0" y2="1">
        <stop offset="0" stop-color="var(--photo-top)"/>
        <stop offset="0.3" stop-color="#dcdcdc"/>
        <stop offset="0.34" stop-color="#9a9a9a"/>
        <stop offset="1" stop-color="var(--photo-floor)"/>
      </linearGradient>
    </defs>
    <rect class="facility-photo" x="0" y="0" width="848" height="560" fill="url(#facility-tones)" role="img" aria-label="Photo of the indoor practice room with turf, wall screens and simulator laptops"/>
    <polygon class="band-dark" points="0,550 848,455 848,1200 0,1200" fill="var(--charcoal)"/>
    <polygon class="band-red" points="0,800 848,713 848,1200 0,1200" fill="var(--red)"/>
  </svg>

  <div class="brand-badge"><span class="brand-name">Fairway Nine Golf</span></div>

  <h1 class="title">Fairway Nine Golf Practice</h1>
  <p class="subtitle">MembershipMembers have 24/7</p>
  <p class="access">access to practice Clearbay &amp; VEX RollBenchOnline scheduling</p>

  <h2 class="options-label">Membership Options</h2>
  <div class="option option-basic"><span class="option-text">$140/month for 4 hours of practice</span></div>
  <div class="option option-unlimited"><span class="option-text">$200/month for unlimited 1 hour of practice</span></div>

  <section class="offer">
    <h2 class="offer-heading">Special Offer</h2>
    <p class="offer-lead">First 20</p>
    <p class="offer-details">who sign up for a<br>full-year membership<br>before the new year<br>save $400</p>
  </section>

  <footer class="contact">
    <span>Contact us for more information: info@fairwayninegolf.com</span>
    <span>www.fairwayninegolf.com</span>
  </footer>
</main>
</body>
</html>
```